maplecrest gymnastics academy

need a website for above to contain information about the academy, enrollment form etc..

Need a web design for new business Maplecrest Gymnastics Academy offering classes in gymnastics. Info on the business is in the doc called "Web design" which details the tabs I will need on my page. Please see our Facebook page to get an idea of the style Maplecrestgymnasticsacademy.

Thank you for your help. I do not require hosting of a domain name just need it all ready to be hosted. Thanks

Budget now increased to include the coding of the website as well.

```html
<!DOCTYPE html>
<html lang="en">
<head>
<meta charset="utf-8">
<title>Maplecrest Gymnastics Academy</title>
<link href="https://fonts.googleapis.com/css2?family=Oswald:wght@400;500&family=Questrial&family=Open+Sans:wght@400;600&display=swap" rel="stylesheet">
<style>
  :root {
    --bg: #000000;
    --bar-edge: #3a3a3a;
    --yellow: #d3c300;
    --yellow-soft: #e4d985;
    --ink: #1c1a05;
    --olive: #5d5413;
    --cream: #fbf6d0;
    --panel-dark: #1e1e1e;
    --white: #ffffff;
    --nav-text: #e6e6e6;
    --dot: #e5501e;
    --rule: rgba(255,255,255,.25);
  }
  * { box-sizing: border-box; margin: 0; padding: 0; }
  html, body { width: 1200px; height: 1173px; overflow: hidden; background: var(--bg); }
  body { position: relative; font-family: "Open Sans", sans-serif; color: var(--white); }
  .abs { position: absolute; }

  /* navigation */
  .nav-bar {
    left: 171px; top: 102px; width: 860px; height: 57px;
    background: linear-gradient(#222, #111);
    border: 2px solid var(--bar-edge); border-radius: 9px;
  }
  .nav-item { top: 119px; font-family: "Questrial", sans-serif; font-size: 17px; color: var(--nav-text); }
  .nav-sep { top: 114px; width: 1px; height: 34px; background: #333; }

  /* brand */
  .brand {
    left: 517px; top: 47px; width: 166px; height: 184px;
    background: var(--yellow); border: 4px solid #3b3b3b; border-radius: 12px;
    display: flex; flex-direction: column; align-items: center; justify-content: center;
    font-family: "Questrial", sans-serif; color: var(--ink); text-align: center;
  }
  .brand-mark { width: 88px; height: 88px; border-radius: 50%; background: var(--yellow-soft); margin-bottom: 8px; }
  .brand-name { font-size: 13px; line-height: 1.3; letter-spacing: .5px; text-transform: uppercase; }

  /* hero */
  .hero-photo {
    left: 130px; top: 215px; width: 830px; height: 452px;
    background: radial-gradient(ellipse at 50% 45%, #7a2a24 0%, #3a1c24 40%, #141420 75%, #000 100%);
  }
  .hero-line { left: 171px; font-family: "Oswald", sans-serif; color: var(--white); letter-spacing: -.5px; }
  .hero-line.big { top: 515px; font-size: 40px; }
  .hero-line.small { top: 576px; font-size: 32px; }
  .dot { top: 642px; width: 11px; height: 11px; border-radius: 50%; background: var(--dot); }
  .dot.active { background: var(--white); border: 2px solid var(--dot); width: 14px; height: 14px; top: 641px; }

  .promo { left: 771px; width: 258px; text-align: center; font-family: "Questrial", sans-serif; }
  .promo.membership { top: 271px; height: 166px; background: var(--yellow-soft); border-radius: 7px 7px 0 0; }
  .promo.coaching { top: 437px; height: 160px; background: var(--panel-dark); border-radius: 0 0 7px 7px; }
  .promo h2 { font-weight: 400; font-size: 35px; }
  .membership h2 { color: var(--white); margin-top: 18px; text-shadow: 0 1px 2px rgba(0,0,0,.25); }
  .coaching h2 { color: var(--yellow-soft); margin-top: 16px; }
  .promo p { font-size: 19px; color: var(--ink); margin-top: 2px; }
  .coaching p { font-size: 13px; color: var(--white); margin-top: 8px; font-family: "Open Sans", sans-serif; font-weight: 600; }
  .promo .btn {
    display: inline-block; width: 193px; height: 38px; line-height: 38px; margin-top: 12px;
    background: var(--yellow); color: var(--white); border-radius: 6px; font-size: 17px;
  }
  .coaching .btn { margin-top: 16px; }

  /* content */
  .content { left: 172px; top: 668px; width: 857px; height: 421px; background: var(--yellow); border-radius: 7px; }
  .col-title { top: 695px; font-family: "Questrial", sans-serif; font-size: 18px; font-weight: 400; color: var(--ink); }
  .photo { background: linear-gradient(135deg, #3b2a6a, #6a4aa0 50%, #2a2236); }
  .item-title { font-family: "Questrial", sans-serif; font-size: 17px; color: var(--olive); }
  .copy { font-size: 12px; line-height: 19px; color: var(--cream); text-align: justify; }
  .more { display: block; font-size: 12px; color: var(--ink); }

  .about { left: 195px; top: 899px; width: 241px; }
  .about .item-title { font-size: 19px; }
  .about .copy { font-size: 13.5px; line-height: 24px; margin-top: 8px; }
  .about .more { margin-top: 12px; }

  .event { left: 590px; width: 150px; }
  .event .copy { margin-top: 8px; }
  .event .more { margin-top: 8px; }
  .event-photo { width: 90px; height: 92px; background: linear-gradient(150deg, #2a3145, #a33030 50%, #8a6a40); }
  .event-date {
    width: 90px; height: 29px; background: #1f1f1f; color: var(--white);
    font-family: "Oswald", sans-serif; font-size: 16px; line-height: 29px; text-align: center;
  }
  .rule { height: 1px; background: var(--rule); }

  .news { left: 781px; top: 733px; width: 227px; }
  .news-item { border-top: 1px solid var(--rule); padding: 18px 0 14px; }
  .news-item .item-title { font-size: 18px; }
  .news-date { display: block; font-size: 12px; color: var(--ink); margin-top: 10px; }
  .news-item .copy { margin-top: 10px; width: 222px; }

  /* footer */
  .footer-text { left: 194px; top: 1117px; font-size: 12.5px; color: var(--white); }
  .follow { left: 848px; top: 1118px; font-family: "Questrial", sans-serif; font-size: 15px; color: var(--white); }
  .social { top: 1114px; width: 26px; height: 26px; border-radius: 50%; }
</style>
</head>
<body>

<nav>
  <div class="abs nav-bar"></div>
  <span class="abs nav-item" style="left:195px">Home</span>
  <span class="abs nav-sep" style="left:257px"></span>
  <span class="abs nav-item" style="left:274px">About Us</span>
  <span class="abs nav-sep" style="left:358px"></span>
  <span class="abs nav-item" style="left:376px">News &amp; Events</span>
  <span class="abs nav-item" style="left:716px">Forms</span>
  <span class="abs nav-sep" style="left:779px"></span>
  <span class="abs nav-item" style="left:796px">Membership</span>
  <span class="abs nav-sep" style="left:902px"></span>
  <span class="abs nav-item" style="left:920px">Contact Us</span>
</nav>

<section class="hero">
  <div class="abs hero-photo" role="img" aria-label="Gymnast in a red leotard performing a split leap in an arena"></div>
  <div class="abs hero-line big">SUCCESS ONLY</div>
  <div class="abs hero-line small">COMES THROUGH TRYING</div>
  <span class="abs dot active" style="left:572px"></span>
  <span class="abs dot" style="left:593px"></span>
  <span class="abs dot" style="left:609px"></span>
  <span class="abs dot" style="left:623px"></span>

  <div class="abs promo membership">
    <h2>MEMBERSHIP</h2>
    <p>JOIN OUR CLUB</p>
    <span class="btn">MEMBERSHIP INFO</span>
  </div>
  <div class="abs promo coaching">
    <h2>COACHING</h2>
    <p>NEED TO IMPROVE YOUR GAME?</p>
    <span class="btn">COACHING INFO</span>
  </div>
</section>

<div class="abs brand">
  <div class="brand-mark"></div>
  <div class="brand-name">Maplecrest<br>Gymnastics Academy</div>
</div>

<main>
  <div class="abs content"></div>

  <h3 class="abs col-title" style="left:195px">ABOUT THE ACADEMY</h3>
  <div class="abs photo" style="left:195px;top:734px;width:241px;height:145px" role="img" aria-label="Gymnast in a purple leotard arching backwards"></div>
  <div class="abs about">
    <div class="item-title">Gymnastics Club</div>
    <p class="copy">MGA is newly established family business whose mission is to provide high quality gymnastics program in a wide variety activities to suit all</p>
    <span class="more">Read More +</span>
  </div>

  <h3 class="abs col-title" style="left:486px">UPCOMING EVENTS</h3>
  <div class="abs event-photo" style="left:485px;top:734px" role="img" aria-label="Gymnast in red performing on the beam"></div>
  <div class="abs event-date" style="left:485px;top:831px">15 &nbsp;Nov</div>
  <div class="abs event" style="top:727px">
    <div class="item-title">New Coaches Corner</div>
    <p class="copy">Lorem ipsum dolor sit amet, consectetur adipi-scing elit, sed do eiusmod tempor incididunt</p>
    <span class="more">Read More +</span>
  </div>
  <div class="abs rule" style="left:485px;top:888px;width:253px"></div>

  <div class="abs event-photo" style="left:485px;top:917px;background:linear-gradient(150deg,#1d2540,#3a4a8a 45%,#b83030 70%,#d8d0c0)" role="img" aria-label="Gymnast in blue and red performing a handstand on the beam"></div>
  <div class="abs event-date" style="left:485px;top:1014px">15 &nbsp;Nov</div>
  <div class="abs event" style="top:910px">
    <div class="item-title">New Coaches Corner</div>
    <p class="copy">Lorem ipsum dolor sit amet, consectetur adipi-scing elit, sed do eiusmod tempor incididunt</p>
    <span class="more">Read More +</span>
  </div>

  <h3 class="abs col-title" style="left:781px">LATEST NEWS</h3>
  <div class="abs news">
    <div class="news-item">
      <div class="item-title">New Coaches Corner</div>
      <span class="news-date">Nov 26,2014</span>
      <p class="copy">MGA is newly established family business whose mission is to provide high quality gymnastics program</p>
    </div>
    <div class="news-item">
      <div class="item-title">New Coaches Corner</div>
      <span class="news-date">Nov 26,2014</span>
      <p class="copy">MGA is newly established family business whose mission is to provide high quality gymnastics program</p>
    </div>
  </div>
</main>

<footer>
  <span class="abs footer-text">Maplecrest Gymnastics Academy © 2014 &nbsp;|&nbsp; Privacy Policy</span>
  <span class="abs follow">FOLLOW</span>
  <span class="abs social" style="left:919px;background:#3b5a9a" aria-label="Social profile one"></span>
  <span class="abs social" style="left:950px;background:#2b9ad6" aria-label="Social profile two"></span>
  <span class="abs social" style="left:981px;background:#c8302a" aria-label="Social profile three"></span>
</footer>

</body>
</html>
```